Marwick Family Chiropractic Stationary

The letterhead and business card must have our logo.
We would like to see the logo used in different ways ( It can be expanded upon in the stationary.)
Please use the the same or similar colors.
Must be eye catching and memorable.
Must be easy to read

Reason: The doctor has been too busy to make any final decisions. He would like to give himself a little more time.

Target Market(s)

Chiropractic Healthcare

Industry/Entity Type

Business

Requirements
Must have
• Dr. Leonard Marwick D.C.
Chiropractor

860-555-0183

417 Birchfield Road, 2nd Floor
Alderbrook, CT 06091

drmarwick@marwickspine.example
www.marwickspine.example
www.facebook.com/MarwickFamilySpine
Should not have
• should not be difficult to read

```html
<!DOCTYPE html>
<html lang="en">
<head>
<meta charset="utf-8">
<title>Marwick Family Chiropractic – Business Cards</title>
<link rel="stylesheet" href="https://fonts.googleapis.com/css2?family=Jost:wght@400;500;600&display=swap">
<style>
  :root {
    --backdrop: #7a4128;
    --card-black: #000000;
    --card-taupe: #7b6f60;
    --leaf-green: #9ccb4f;
    --bark-grey: #a49a8a;
    --text-light: #f2f2f2;
    --rule-grey: #8a8a8a;
    --pattern-dark: #14160d;
    --pattern-mid: #262b16;
  }
  * { margin: 0; padding: 0; box-sizing: border-box; }
  html, body { width: 1200px; height: 716px; overflow: hidden; }
  body {
    background: var(--backdrop);
    font-family: "Jost", sans-serif;
    position: relative;
  }
  .card {
    position: absolute;
    width: 544px;
    height: 308px;
    border-radius: 22px;
    overflow: hidden;
  }
  .card--contact { left: 43px; top: 37px; background: var(--card-black); }
  .card--mark { left: 619px; top: 35px; background: var(--card-black); }
  .card--name { left: 43px; top: 372px; background: var(--card-black); }
  .card--mark-taupe { left: 619px; top: 367px; background: var(--card-taupe); }

  /* brand block */
  .brand { position: absolute; text-align: center; color: var(--leaf-green); font-weight: 600; }
  .brand__dot { display: block; margin: 0 auto; border-radius: 50%; background: var(--leaf-green); }
  .brand__name { display: block; text-transform: uppercase; line-height: 1.05; }
  .brand__name small { display: block; font-size: 0.42em; letter-spacing: 0.5px; margin-top: 4px; }

  .card--contact .brand { left: 40px; top: 52px; width: 200px; }
  .card--contact .brand__dot { width: 112px; height: 112px; margin-bottom: 22px; }
  .card--contact .brand__name { font-size: 32px; }

  .contact {
    position: absolute;
    left: 278px; top: 52px;
    border-left: 1.5px solid var(--rule-grey);
    padding-left: 12px;
    height: 194px;
    color: var(--text-light);
    font-size: 14px;
    line-height: 1.5;
  }
  .contact__name { color: var(--leaf-green); font-size: 17px; font-weight: 500; line-height: 1.2; }
  .contact__role { color: var(--bark-grey); font-size: 15px; margin-bottom: 12px; }
  .contact__list { list-style: none; margin-bottom: 10px; }
  .contact__list li { display: flex; align-items: center; gap: 6px; }
  .contact__list svg { width: 11px; height: 11px; flex: none; }
  .contact__address { font-style: normal; line-height: 1.4; }

  .card--mark .brand,
  .card--mark-taupe .brand { left: 0; right: 0; top: 32px; }
  .card--mark .brand__dot,
  .card--mark-taupe .brand__dot { width: 170px; height: 170px; margin-bottom: 12px; }
  .card--mark .brand__name,
  .card--mark-taupe .brand__name { font-size: 16px; letter-spacing: 0.5px; }
  .card--mark-taupe .brand { color: #ffffff; }
  .card--mark-taupe .brand__dot { background: #ffffff; }

  .web {
    position: absolute; left: 0; right: 0; bottom: 28px;
    text-align: center; color: var(--text-light);
    font-size: 15px; letter-spacing: 2.5px;
  }

  .pattern {
    position: absolute; inset: 0;
    background: radial-gradient(circle at 50% 50%, var(--pattern-mid) 0%, var(--pattern-dark) 80%);
  }
  .card--name .brand { left: 0; right: 0; top: 84px; color: var(--leaf-green); }
  .card--name .brand__name { font-size: 76px; letter-spacing: 1px; }
  .card--name .brand__name small { font-size: 30px; margin-top: 2px; }
</style>
</head>
<body>

  <section class="card card--contact">
    <div class="brand">
      <span class="brand__dot"></span>
      <span class="brand__name">Marwick<small>Family Chiropractic</small></span>
    </div>
    <div class="contact">
      <p class="contact__name">Dr. Leonard Marwick D.C.</p>
      <p class="contact__role">Chiropractor</p>
      <ul class="contact__list">
        <li><svg viewBox="0 0 12 12"><path d="M3 1 L5 3.5 L4 5 Q5.5 7 7 8 L8.5 7 L11 9 L9.5 11 Q4 10 1 2.5 Z" fill="#f2f2f2"/></svg>860-555-0183</li>
        <li><svg viewBox="0 0 12 12"><rect x="1" y="3" width="10" height="7" fill="#f2f2f2"/><path d="M1 3 L6 7 L11 3" stroke="#000" fill="none"/></svg>mymarwick@marwickspine.example</li>
        <li><svg viewBox="0 0 12 12"><circle cx="6" cy="6" r="5" fill="none" stroke="#f2f2f2"/><path d="M1 6 H11 M6 1 V11" stroke="#f2f2f2"/></svg>www.marwickspine.example</li>
        <li><svg viewBox="0 0 12 12"><rect x="1" y="1" width="10" height="10" fill="#3b5ea8"/></svg>MarwickFamilySpine</li>
      </ul>
      <address class="contact__address">417 Birchfield Road<br>2nd Floor, Alderbrook, CT 06091</address>
    </div>
  </section>

  <section class="card card--mark">
    <div class="brand">
      <span class="brand__dot"></span>
      <span class="brand__name">Marwick Family Chiropractic</span>
    </div>
    <p class="web">www.marwickspine.example</p>
  </section>

  <section class="card card--name">
    <div class="pattern" role="img" aria-label="Repeating pattern of small tree marks on black"></div>
    <div class="brand">
      <span class="brand__name">Marwick<small>Family Chiropractic</small></span>
    </div>
    <p class="web">www.marwickspine.example</p>
  </section>

  <section class="card card--mark-taupe">
    <div class="brand">
      <span class="brand__dot"></span>
      <span class="brand__name">Marwick Family Chiropractic</span>
    </div>
    <p class="web">www.marwickspine.example</p>
  </section>

</body>
</html>
```